Satchel & Sundial needs new business card design

I need a new business card design. I'm looking for out-of-the-box design which represents the freedom of being a location independent entrepreneur.
I offer coaching, retreats and trips.
I would like to see designs with and without the photo.
Colors I use are black (#000000), green (#25A796) and brown (#D7C38C)
Website satchelandsundial.example

Target Market(s)

location independent entrepreneurs, digital nomads, people looking to swap the 9 to 5 for a lifestyle business

Industry/Entity Type

Business

Contact Information for Business Card

Dorota Falkner
Your Lifestyle Business Coach, Retreat & Trip Leader
http://satchelandsundial.example
hello@satchelandsundial.example
Live a life you don't need a holiday from

Font styles to use
Serif
Sans Serif

Requirements
Must have
• One side should contain only the logo. I would also consider having the "Live a life you don't need a holiday from" on that side too (depending on how it looks)
• Please show both sides on the designs.

```html
<!DOCTYPE html>
<html lang="en">
<head>
<meta charset="utf-8">
<title>Satchel &amp; Sundial – Business Card</title>
<link rel="stylesheet" href="https://fonts.googleapis.com/css2?family=Oswald:wght@300;400;500&display=swap">
<style>
  :root {
    --backdrop: #e4e4e4;
    --card-light: #f7f7f7;
    --card-light-edge: #e9e9e9;
    --card-dark: #161616;
    --ink: #111111;
    --green: #25a796;
    --gold: #d7c38c;
    --white: #ffffff;
  }
  * { margin: 0; padding: 0; box-sizing: border-box; }
  html, body {
    width: 1200px;
    height: 576px;
    overflow: hidden;
    background: var(--backdrop);
  }
  .card {
    position: absolute;
    top: 139px;
    width: 484px;
    height: 293px;
    border-radius: 8px;
    overflow: hidden;
  }
  .card--front {
    left: 82px;
    background: linear-gradient(180deg, var(--card-light) 0%, var(--card-light-edge) 100%);
  }
  .card--back {
    left: 602px;
    width: 480px;
    background: var(--card-dark);
  }
  .brand-name {
    position: absolute;
    left: 0;
    right: 0;
    top: 118px;
    text-align: center;
    font-family: "Oswald", sans-serif;
    font-weight: 400;
    font-size: 40px;
    letter-spacing: 1px;
    text-transform: uppercase;
    color: var(--ink);
  }
  .back-art {
    position: absolute;
    inset: 0;
  }
  .person-name {
    position: absolute;
    left: 28px;
    top: 34px;
    font-family: "Oswald", sans-serif;
    font-weight: 500;
    font-size: 20px;
    color: var(--gold);
    text-transform: uppercase;
    letter-spacing: 0.2px;
  }
  .person-role {
    position: absolute;
    left: 28px;
    top: 61px;
    font-family: "Oswald", sans-serif;
    font-weight: 400;
    font-size: 11.5px;
    line-height: 14px;
    color: var(--white);
  }
  .contact-list {
    position: absolute;
    left: 28px;
    top: 153px;
    list-style: none;
    font-family: "Oswald", sans-serif;
    font-weight: 300;
    font-size: 12px;
    color: var(--white);
  }
  .contact-item {
    display: flex;
    align-items: center;
    height: 20px;
  }
  .contact-icon {
    width: 11px;
    height: 11px;
    margin-right: 8px;
    flex: none;
  }
  .contact-item .accent { color: var(--gold); }
  .tagline {
    position: absolute;
    left: 28px;
    top: 236px;
    font-family: "Oswald", sans-serif;
    font-weight: 400;
    font-size: 13px;
    color: var(--gold);
  }
</style>
</head>
<body>

<section class="card card--front" aria-label="Business card front">
  <div class="brand-name">Satchel &amp; Sundial</div>
</section>

<section class="card card--back" aria-label="Business card back">
  <svg class="back-art" width="480" height="293" viewBox="0 0 480 293">
    <defs>
      <linearGradient id="photoTones" x1="0" y1="0" x2="0" y2="1">
        <stop offset="0" stop-color="#8a9a6a"/>
        <stop offset="0.45" stop-color="#5f7447"/>
        <stop offset="1" stop-color="#6d6448"/>
      </linearGradient>
    </defs>
    <path d="M322 0 Q252 150 296 293" fill="none" stroke="var(--green)" stroke-width="5"/>
    <path d="M328 0 H480 V293 H302 Q262 150 328 0 Z" fill="url(#photoTones)"
          role="img" aria-label="Photo of the coach outdoors among trees, holding a small hashtag sign"/>
  </svg>

  <div class="person-name">Dorota Falkner</div>
  <div class="person-role">Your Lifestyle Business Coach<br>Retreat &amp; Trip Leader</div>

  <ul class="contact-list">
    <li class="contact-item">
      <svg class="contact-icon" viewBox="0 0 12 12"><rect x="0.5" y="2" width="11" height="8" fill="var(--green)"/><path d="M0.5 2 L6 6.5 L11.5 2" fill="none" stroke="var(--card-dark)" stroke-width="1.2"/></svg>
      hello@satchelandsundial.example
    </li>
    <li class="contact-item">
      <svg class="contact-icon" viewBox="0 0 12 12"><circle cx="6" cy="6" r="5" fill="none" stroke="var(--green)" stroke-width="1.3"/><ellipse cx="6" cy="6" rx="2" ry="5" fill="none" stroke="var(--green)" stroke-width="1"/><path d="M1 6 H11" stroke="var(--green)" stroke-width="1"/></svg>
      <span>www.<span class="accent">satchelandsundial</span>.example</span>
    </li>
    <li class="contact-item">
      <svg class="contact-icon" viewBox="0 0 12 12"><rect x="1" y="1" width="10" height="10" fill="var(--green)"/></svg>
      /satchelandsundial
    </li>
  </ul>

  <div class="tagline">Live a life you don't need a holiday from</div>
</section>

</body>
</html>
```